Satchel & Sundial needs new business card design

I need a new business card design. I'm looking for out-of-the-box design which represents the freedom of being a location independent entrepreneur.
I offer coaching, retreats and trips.
I would like to see designs with and without the photo.
Colors I use are black (#000000), green (#25A796) and brown (#D7C38C)
Website satchelandsundial.example

Target Market(s)

location independent entrepreneurs, digital nomads, people looking to swap the 9 to 5 for a lifestyle business

Industry/Entity Type

Business

Contact Information for Business Card

Dorota Falkner
Your Lifestyle Business Coach, Retreat & Trip Leader
http://satchelandsundial.example
hello@satchelandsundial.example
Live a life you don't need a holiday from

Font styles to use
Serif
Sans Serif

Requirements
Must have
• One side should contain only the logo. I would also consider having the "Live a life you don't need a holiday from" on that side too (depending on how it looks)
• Please show both sides on the designs.

```html
<!DOCTYPE html>
<html lang="en">
<head>
<meta charset="utf-8">
<title>Satchel &amp; Sundial – Business Card</title>
<link rel="stylesheet" href="https://fonts.googleapis.com/css2?family=PT+Sans:wght@400;700&family=PT+Sans+Narrow:wght@700&display=swap">
<style>
  :root {
    --backdrop: #d6d6d8;
    --card-white: #ececee;
    --ink: #1c1c1c;
    --ink-soft: #3a3a3a;
    --teal: #1f9a88;
    --sand: #b9a774;
    --sand-deep: #ad9b68;
  }
  html, body {
    margin: 0;
    padding: 0;
    width: 1105px;
    height: 1200px;
    overflow: hidden;
    background: var(--backdrop);
  }
  .canvas {
    position: relative;
    width: 1105px;
    height: 1200px;
  }
  .card {
    position: absolute;
    left: 182px;
    width: 746px;
    height: 427px;
    overflow: hidden;
  }
  .card--front { top: 119px; background: var(--card-white); }
  .card--back  { top: 636px; background: var(--sand); }

  .wordmark {
    position: absolute;
    margin: 0;
    font-family: "PT Sans Narrow", "PT Sans", sans-serif;
    font-weight: 700;
    text-transform: uppercase;
    letter-spacing: 1px;
    color: var(--ink);
    line-height: 1;
    white-space: nowrap;
  }
  .card--front .wordmark {
    right: 56px;
    top: 62px;
    font-size: 48px;
  }

  .accent-bar {
    position: absolute;
    left: 0;
    top: 203px;
    width: 14px;
    height: 186px;
    background: var(--sand);
  }
  .contact {
    position: absolute;
    left: 55px;
    top: 200px;
    font-family: "PT Sans", sans-serif;
  }
  .contact__name {
    margin: 0;
    font-size: 25px;
    font-weight: 700;
    letter-spacing: 0.5px;
    text-transform: uppercase;
    color: var(--teal);
    line-height: 1.2;
  }
  .contact__role {
    margin: 4px 0 0;
    font-size: 20px;
    line-height: 27px;
    color: var(--ink);
  }
  .contact__links {
    list-style: none;
    margin: 12px 0 0;
    padding: 0;
    font-size: 19px;
    line-height: 28px;
    color: var(--ink-soft);
  }
  .contact__links li {
    display: flex;
    align-items: center;
    gap: 9px;
  }
  .contact__links svg { width: 18px; height: 18px; flex: none; }
  .contact__tagline {
    margin: 10px 0 0;
    font-family: "PT Sans Narrow", sans-serif;
    font-weight: 700;
    font-size: 19px;
    text-transform: uppercase;
    color: var(--teal);
    letter-spacing: 0.2px;
  }

  .back-pattern {
    position: absolute;
    inset: 0;
    background: linear-gradient(160deg, var(--sand) 0%, var(--sand-deep) 100%);
  }
  .card--back .wordmark {
    left: 0;
    right: 0;
    top: 178px;
    text-align: center;
    font-size: 60px;
  }
</style>
</head>
<body>
<main class="canvas">

  <section class="card card--front" aria-label="Card front">
    <p class="wordmark">Satchel &amp; Sundial</p>
    <div class="accent-bar"></div>
    <div class="contact">
      <h1 class="contact__name">Dorota Falkner</h1>
      <p class="contact__role">Your Lifestyle Business Coach<br>Retreat &amp; Trip Leader</p>
      <ul class="contact__links">
        <li>
          <svg viewBox="0 0 18 18" aria-hidden="true">
            <rect x="1" y="4" width="16" height="11" fill="var(--teal)"/>
            <path d="M1.5 4.5 L9 10 L16.5 4.5" fill="none" stroke="var(--card-white)" stroke-width="1.4"/>
          </svg>
          hello@satchelandsundial.example
        </li>
        <li>
          <svg viewBox="0 0 18 18" aria-hidden="true">
            <circle cx="9" cy="9" r="8" fill="var(--teal)"/>
            <ellipse cx="9" cy="9" rx="3.5" ry="8" fill="none" stroke="var(--card-white)" stroke-width="1.2"/>
            <line x1="1" y1="9" x2="17" y2="9" stroke="var(--card-white)" stroke-width="1.2"/>
          </svg>
          www.satchelandsundial.example
        </li>
      </ul>
      <p class="contact__tagline">Live a life you don’t need a holiday from</p>
    </div>
  </section>

  <section class="card card--back" aria-label="Card back">
    <div class="back-pattern" role="img" aria-label="Faint repeating brand lettering pattern across the sand background"></div>
    <p class="wordmark">Satchel &amp; Sundial</p>
  </section>

</main>
</body>
</html>
```